Business card for a Exhibition booth fabrication company

Hi. My company would like to change our corporate name card. We are an events and Exhibition stand builder company. We would like our corporate name card to resonate what we do. I need someone to create something unique that relates to the industry that I am in. The graphic designer should be creative to incorporate the elements of my industry and try to blend in well in the design of the card. Our aim is to ensure that we are unique and our card can look different from our competitors.
Updates

Target Market(s)

Marketing and events manager from all companies

Contact Information for Business Card

The business card should have the following details:
Name
Job Title
Email
Website

Colors

Designer to choose colors to be used in the design.

Requirements
Must have
• The card must be look something that is relevant to the service that I am providing. My website is: www.velmora-buildworks.com
• You can see my website to get more information on what service that I am doing
Nice to have
• On the back of my card, I would like to have a globe image with the incorporation of my company logo. This is to indicate that my services can be done in any part of the world.

```html
<!DOCTYPE html>
<html lang="en">
<head>
<meta charset="utf-8">
<title>Velmora Buildworks – Business Card</title>
<link href="https://fonts.googleapis.com/css2?family=Open+Sans:wght@400;600;700&display=swap" rel="stylesheet">
<style>
  :root {
    --bg: #e6e2df;
    --card: #ffffff;
    --red: #e8202a;
    --grey: #5a5b5d;
    --ink: #3a3b3d;
    --rule: #4a4a4a;
    --map: #e9e9ea;
  }
  * { box-sizing: border-box; margin: 0; padding: 0; }
  html, body { width: 1200px; height: 997px; overflow: hidden; }
  body {
    background: var(--bg);
    font-family: "Open Sans", Arial, sans-serif;
    color: var(--ink);
    position: relative;
  }
  .card {
    position: absolute;
    width: 540px;
    height: 309px;
    background: var(--card);
    box-shadow: 0 6px 18px rgba(0,0,0,0.12);
    overflow: hidden;
  }
  .card--front { left: 40px; top: 344px; }
  .card--back { left: 620px; top: 344px; }

  .brand {
    position: absolute;
    display: flex;
    align-items: center;
    gap: 12px;
  }
  .brand__dot {
    width: 30px; height: 30px;
    border-radius: 50%;
    background: var(--red);
  }
  .brand__name {
    font-weight: 700;
    font-size: 22px;
    letter-spacing: 2.5px;
    color: var(--ink);
  }
  .card--front .brand { left: 34px; top: 92px; }
  .card--back .brand { left: 50%; top: 50%; transform: translate(-50%, -50%); }

  .edge-band {
    position: absolute; right: 0; top: 0;
    width: 14px; height: 100%;
    background: var(--red);
  }
  .edge-block {
    position: absolute; right: 0; top: 92px;
    width: 26px; height: 24px;
    background: var(--grey);
  }
  .rule {
    position: absolute; left: 34px; right: 40px; top: 168px;
    height: 1px; background: var(--rule);
  }
  .person {
    position: absolute; right: 36px; top: 96px;
    text-align: right; line-height: 1.15;
  }
  .person__name { font-weight: 700; font-size: 15px; color: var(--ink); }
  .person__title { font-size: 12px; color: var(--red); }
  .address {
    position: absolute; right: 36px; top: 180px;
    text-align: right; font-size: 11.5px; line-height: 1.5; color: var(--ink);
  }
  .contacts {
    position: absolute; left: 34px; bottom: 30px;
    list-style: none; font-size: 12px; line-height: 1.6;
  }
  .contacts li { display: flex; align-items: center; gap: 8px; }
  .contacts svg { width: 10px; height: 10px; fill: var(--red); }

  .world-map {
    position: absolute; left: 60px; top: 40px;
    width: 420px; height: 230px;
    border-radius: 50% 50% 40% 40%;
    background: radial-gradient(ellipse at center, var(--map) 0%, #f3f3f3 60%, var(--card) 100%);
  }
</style>
</head>
<body>
  <section class="card card--front">
    <div class="edge-band"></div>
    <div class="edge-block"></div>
    <div class="brand">
      <span class="brand__dot"></span>
      <span class="brand__name">VELMORA BUILDWORKS</span>
    </div>
    <div class="person">
      <div class="person__name">Daniel Hart</div>
      <div class="person__title">President</div>
    </div>
    <div class="rule"></div>
    <div class="address">P.O. Box 2184, Bin Omran,<br>Street Doha - Qatar</div>
    <ul class="contacts">
      <li><svg viewBox="0 0 10 10"><path d="M2 1h2l1 2-1.2 1a5 5 0 0 0 2.2 2.2L7 5l2 1v2a1 1 0 0 1-1 1A8 8 0 0 1 1 2a1 1 0 0 1 1-1z"/></svg>+974 55501284</li>
      <li><svg viewBox="0 0 10 10"><path d="M0 2h10v6H0z M0 2l5 3.5L10 2" stroke="#fff" stroke-width="0.8"/></svg>info@velmora-buildworks.com</li>
      <li><svg viewBox="0 0 10 10"><circle cx="5" cy="5" r="5"/></svg>www.velmora-buildworks.com</li>
    </ul>
  </section>

  <section class="card card--back">
    <div class="world-map" role="img" aria-label="Faint grey world map behind the company name"></div>
    <div class="brand">
      <span class="brand__dot"></span>
      <span class="brand__name">VELMORA BUILDWORKS</span>
    </div>
  </section>
</body>
</html>
```